Upland Bird Hunting Preserve and Pointing Dog kennel

Need Price packages outlined for the bird hunting business. List the kennel and that we provide training and dogs for sale.
The preserve is "Tall Heron Provisions" the dog kennel is "Pine Hollow Setters"
1/2 Day Upland Field Hunts: 5 Pheasants $120
7 Chukar $125
Continental Hunt 12 Pheasants $325 includes meal, minimum 12 hunters
Guides available $100

Target Market(s)

upland bird hunters

Industry/Entity Type

hunting, outdoor

Colors
EE7325
F08F49
F5BC92
FAE3D3
FDF4ED

```html
<!DOCTYPE html>
<html lang="en">
<head>
<meta charset="utf-8">
<title>Tall Heron Provisions – Upland Hunts</title>
<link rel="stylesheet" href="https://fonts.googleapis.com/css2?family=Anton&family=Crimson+Text&family=Rubik+Dirt&display=swap">
<style>
:root{
  --gold:#b9a04a;
  --gold-deep:#8f7a33;
  --gold-light:#d9c27a;
  --ink:#0d0d0b;
  --paper:#ffffff;
  --backdrop:#f2f0ea;
}
*{margin:0;padding:0;box-sizing:border-box}
html,body{width:1200px;height:1200px;overflow:hidden;background:var(--backdrop)}
.flyer{position:absolute;left:120px;top:0;width:960px;height:1200px;background:linear-gradient(180deg,#c1a852 0%,var(--gold) 55%,#a88f3f 100%);overflow:hidden;font-family:"Anton",sans-serif;color:var(--ink);text-transform:uppercase}
.abs{position:absolute}
.brand-title{left:0;width:960px;top:40px;text-align:center;font-family:"Rubik Dirt",sans-serif;font-size:124px;line-height:1;color:var(--paper)}
.brand-sub{left:0;width:960px;top:178px;text-align:center;font-size:52px;letter-spacing:20px;line-height:1}
.rule{height:2px;background:var(--gold-light)}
.location{left:0;width:960px;top:252px;text-align:center;font-size:26px;line-height:1.2;color:var(--paper)}
.preserve-line{left:0;width:960px;top:290px;text-align:center;font-size:46px;line-height:1.1}
.hunter-art{left:40px;top:365px;width:360px;height:375px}
.target-art{width:100px;height:100px}
.badge{left:620px;top:360px;width:190px;height:190px}
.field-hunts{left:430px;top:420px;font-size:40px;line-height:1.05;color:var(--paper);text-align:right;width:170px}
.half-day{left:420px;top:560px;background:var(--gold-light);padding:4px 22px;font-size:34px;line-height:1.2}
.price-table{left:600px;top:556px;width:330px}
.price-row{display:flex;justify-content:space-between;font-size:30px;line-height:1.2;border-bottom:2px solid var(--gold-light);padding:2px 0}
.guide{left:590px;top:702px;display:flex;font-size:22px;line-height:1.2}
.guide span{padding:3px 14px}
.guide .label{background:var(--paper)}
.guide .value{background:var(--ink);color:var(--paper)}
.ground{left:0;top:748px;width:960px;height:452px}
.section-head{font-size:34px;line-height:1.05;color:var(--paper)}
.section-head .accent{color:var(--gold);display:block}
.big-price{font-size:64px;color:var(--paper);line-height:1}
.big-price sup{font-size:26px;vertical-align:top}
.per{display:inline-block;font-size:18px;line-height:1;color:var(--paper);vertical-align:middle;margin-left:6px}
.note{font-size:17px;line-height:1.15;color:var(--gold)}
.note b{color:var(--paper);font-weight:400}
.serif{font-family:"Crimson Text",serif;text-transform:none;color:var(--paper);font-size:21px;line-height:1.2}
.dots{border-top:3px dotted #444}
.minimum{left:285px;top:875px;width:92px;height:92px;border-radius:50%;background:var(--gold);text-align:center;font-size:13px;line-height:1;padding-top:16px}
.minimum b{display:block;font-size:32px;font-weight:400}
.footer-main{left:150px;top:1075px;width:560px;text-align:center;color:var(--gold);font-size:24px;line-height:1.2}
.footer-sub{left:150px;top:1108px;width:560px;text-align:center;color:var(--paper);font-size:16px;line-height:1.2}
.contact{left:150px;top:1140px;width:560px;text-align:center;color:var(--gold);font-size:30px;line-height:1.2}
.contact .phone{margin-left:30px}
.mark{font-family:"Crimson Text",serif;text-transform:uppercase;color:var(--paper);font-size:17px;line-height:1.1;text-align:center}
</style>
</head>
<body>
<main class="flyer">
  <h1 class="abs brand-title">Tall Heron</h1>
  <p class="abs brand-sub">Provisions</p>
  <div class="abs rule" style="left:190px;top:268px;width:170px"></div>
  <div class="abs rule" style="left:600px;top:268px;width:170px"></div>
  <p class="abs location">Alder Falls, MO</p>
  <p class="abs preserve-line">Licensed Shooting Preserve</p>

  <svg class="abs hunter-art" role="img" aria-label="Silhouette of a hunter aiming a shotgun beside a pointing dog in tall grass" viewBox="0 0 360 375">
    <defs><linearGradient id="silhouette" x1="0" y1="0" x2="0" y2="1"><stop offset="0" stop-color="#6b5b25"/><stop offset="1" stop-color="#1c180c"/></linearGradient></defs>
    <rect width="360" height="375" rx="6" fill="url(#silhouette)"/>
  </svg>

  <svg class="abs target-art" style="left:845px;top:300px" role="img" aria-label="Flying quail inside a crosshair" viewBox="0 0 100 100"><circle cx="50" cy="50" r="44" fill="#a38c3d"/></svg>
  <svg class="abs target-art" style="left:855px;top:410px" role="img" aria-label="Flying quail inside a crosshair" viewBox="0 0 100 100"><circle cx="50" cy="50" r="44" fill="#a38c3d"/></svg>

  <svg class="abs badge" viewBox="0 0 190 190" aria-hidden="true"><circle cx="95" cy="95" r="90" fill="#a99043"/></svg>

  <p class="abs field-hunts">Upland<br>Field<br>Hunts</p>

  <div class="abs half-day">Half Day</div>
  <div class="abs price-table">
    <div class="price-row"><span>5 Pheasants</span><span>$120</span></div>
    <div class="price-row"><span>7 Chukar</span><span>$125</span></div>
    <div class="price-row"><span>8 Quail</span><span>$100</span></div>
  </div>
  <div class="abs guide"><span class="label">Guide Available</span><span class="value">$100 Per Half Day</span></div>

  <svg class="abs ground" viewBox="0 0 960 452" preserveAspectRatio="none" aria-hidden="true">
    <path d="M0 10 L40 0 L80 14 L140 4 L200 18 L260 6 L320 20 L380 10 L440 26 L500 36 L560 30 L620 44 L680 34 L740 48 L800 30 L860 40 L920 20 L960 10 L960 452 L0 452 Z" fill="var(--ink)"/>
  </svg>

  <h2 class="abs section-head" style="left:95px;top:775px">Continental<span class="accent">Pheasant Hunt</span></h2>
  <div class="abs dots" style="left:95px;top:858px;width:210px"></div>
  <p class="abs big-price" style="left:90px;top:868px"><sup>$</sup>325<span class="per">Per<br>Hunter</span></p>
  <p class="abs note" style="left:90px;top:944px">Includes 12 Pheasants<br>Per Hunter &amp; Meal</p>
  <svg class="abs" style="left:335px;top:765px;width:140px;height:105px" role="img" aria-label="Pheasant illustration with a crosshair" viewBox="0 0 140 105"><rect width="140" height="105" rx="8" fill="var(--gold-deep)"/></svg>
  <div class="abs minimum"><b>12</b>Hunter<br>Minimum</div>
  <p class="abs serif" style="left:80px;top:990px">All hunts include bird cleaning<br>Lodging available, call for pricing</p>

  <h2 class="abs section-head" style="left:520px;top:810px">Guided Spring<span class="accent">Turkey Hunts</span></h2>
  <div class="abs dots" style="left:520px;top:892px;width:200px"></div>
  <svg class="abs" style="left:750px;top:800px;width:130px;height:100px" role="img" aria-label="Wild turkey illustration with a crosshair" viewBox="0 0 130 100"><rect width="130" height="100" rx="8" fill="var(--gold-deep)"/></svg>
  <p class="abs note" style="left:520px;top:905px"><b>3 Day</b> Hunt Includes<br>Meals &amp; Lodging</p>
  <p class="abs big-price" style="left:690px;top:905px;font-size:52px"><sup>$</sup>1600<span class="per">Per<br>Hunter</span></p>
  <p class="abs serif" style="left:500px;top:972px">Guided Whitetail Deer Hunts - Rifle &amp; Archery</p>
  <p class="abs note" style="left:500px;top:1010px"><b>5 Day</b> Hunt Includes<br>Meals &amp; Lodging</p>
  <p class="abs big-price" style="left:680px;top:1008px;font-size:52px"><sup>$</sup>2750<span class="per">Per<br>Hunter</span></p>

  <div class="abs dots" style="left:160px;top:1062px;width:540px"></div>
  <p class="abs footer-main">We provide training and dogs for sale.</p>
  <p class="abs footer-sub">Puppies and started dogs available!</p>
  <p class="abs contact"><span class="name">Dale Morrow</span><span class="phone">555-014-7720</span></p>

  <p class="abs mark" style="left:40px;top:1100px;width:110px">Tall Heron<br>Provisions</p>
  <p class="abs mark" style="left:740px;top:1130px;width:190px">Pine Hollow Setters</p>
</main>
</body>
</html>
```